eCommerce website for a DIY shop & communal center

We need a website for a business called The Maple Bench. The Maple Bench is both a shop and communal establishment where people with shared interests, especially in DIY (Do It Yourself) and crafting, can gather to shop for & work on projects while sharing ideas, equipment, supplies and knowledge. The shop is both brick & motor and online. The physical communal space provides workstations, equipment, tools and supplies and expertise for DIY lovers to create their projects.

Target Market(s)

Middle & upper class DIY enthusiasts, creative hobbyists, budding artists & small business owners

Industry/Entity Type

DIY, Arts & Crafts

Coding

Coded - Design and coding required

Number of Pages Required

5+ page

Requirements
Must have
• Menus to include 1. home page (with about us, operating hours, contacts, location, meet the team); 2. Bench activities (how to DIY at the Bench, booking, equipment & tools, house rules); 3. Bench events (events in the Bench, offsite events); 4. Resources (FAQs, tutorials, blogs, eBooks) and 5. Online shop
Nice to have
• Branding guidelines eg logo colours (see attachment) to influence design. Tillpost shop. Booking feature for activities & events at the Bench.

```html
<!DOCTYPE html>
<html lang="en">
<head>
<meta charset="utf-8">
<title>The Maple Bench – Bench Events</title>
<link href="https://fonts.googleapis.com/css2?family=Roboto:ital,wght@0,400;0,500;0,700;1,400&family=Great+Vibes&display=swap" rel="stylesheet">
<style>
:root{
  --orange:#f07f3a;
  --blue:#2b8fd6;
  --pink:#e0457a;
  --ink:#111;
  --text:#444;
  --muted:#666;
  --line:#e3e3e3;
  --footer:#0b0b0b;
  --white:#fff;
}
*{margin:0;padding:0;box-sizing:border-box}
html,body{width:667px;height:1200px;overflow:hidden;background:var(--white)}
body{position:relative;font-family:'Roboto',Arial,sans-serif;color:var(--text)}
.abs{position:absolute}

/* header */
.topbar{left:0;top:0;width:667px;height:27px;border-bottom:1px solid var(--line)}
.phone{left:56px;top:3px;display:flex;align-items:center;gap:7px;font-size:8.5px;color:var(--ink)}
.phone-ico{width:21px;height:21px;border:1px solid #999;border-radius:50%;display:flex;align-items:center;justify-content:center}
.socials-top{right:56px;top:3px;display:flex;gap:3px}
.socials-top span{width:21px;height:21px;border:1px solid #888;border-radius:50%}
.nav{top:36px;font-size:8.5px;color:var(--ink);letter-spacing:.1px}
.brand{left:290px;top:0;width:86px;height:74px;background:var(--white);border-radius:0 0 43px 43px;display:flex;flex-direction:column;align-items:center;justify-content:center;z-index:3}
.brand-name{font-size:10px;font-weight:700;color:var(--orange);text-align:center;line-height:1.15;margin-top:-6px}
.brand-dot{width:8px;height:8px;background:var(--blue);border-radius:50%;margin-bottom:4px}

/* hero */
.hero{left:0;top:56px;width:667px;height:164px;background:linear-gradient(100deg,#4a2e22 0%,#7a4a30 40%,#9b5f3e 62%,#5a3a2a 100%)}
.hero-title{left:57px;top:104px;font-size:30px;font-weight:700;color:var(--white);letter-spacing:.3px}

/* workshops */
.script{font-family:'Great Vibes',cursive;font-weight:400}
.ws-title{left:0;top:266px;width:667px;text-align:center;font-size:29px}
.o{color:var(--orange)}.b{color:var(--blue)}.p{color:var(--pink)}
.ws-lead{left:150px;top:311px;width:367px;text-align:center;font-size:8.2px;line-height:13.6px;color:var(--muted)}
.card{top:358px;width:178px;height:300px;background:var(--white);box-shadow:0 0 6px rgba(0,0,0,.08)}
.card-img{left:0;top:0;width:178px;height:126px}
.date{left:2px;top:110px;width:111px;height:23px;background:var(--blue);color:var(--white);font-size:7px;display:flex;align-items:center;justify-content:center;gap:3px}
.card h3{left:7px;top:140px;font-size:11.8px;font-weight:500;color:var(--ink)}
.card .desc{left:6px;top:159px;width:168px;font-size:7.2px;line-height:13.2px;color:var(--muted)}
.card .obj{left:6px;top:202px;font-size:7.4px;font-style:italic;color:var(--ink)}
.card .obj-t{left:6px;top:216px;font-size:7.2px;color:var(--muted)}
.avatar{left:6px;top:233px;width:31px;height:31px;border-radius:50%}
.host{left:44px;top:238px;font-size:7.5px;color:var(--ink)}
.host-role{left:45px;top:250px;font-size:6.6px;color:var(--muted)}
.btn{background:var(--orange);color:var(--white);font-size:7.8px;font-weight:700;border-radius:14px;display:flex;align-items:center;justify-content:center;letter-spacing:.2px}
.card .btn{left:39px;top:284px;width:100px;height:26px}
.arrow{top:512px}

/* private events */
.pe-wash{left:330px;top:712px;width:310px;height:262px;background:radial-gradient(ellipse at 55% 50%,rgba(120,200,210,.35),rgba(120,200,210,.12) 55%,rgba(255,255,255,0) 75%)}
.pe-img{left:56px;top:723px;width:278px;height:230px;background:linear-gradient(160deg,#2d4a2c 0%,#3f5f3a 35%,#5b5a50 60%,#2b2a2a 100%)}
.pe-title{left:355px;top:718px;font-size:33px;line-height:31px}
.pe-text{left:357px;top:797px;font-size:8.6px;line-height:17.4px;color:#333;white-space:nowrap}
.pe-btn{left:354px;top:932px;width:100px;height:26px}

/* footer */
.footer{left:0;top:1005px;width:667px;height:195px;background:var(--footer);color:var(--white)}
.fcol h4{font-size:9.4px;font-weight:500;margin-bottom:6px;letter-spacing:.1px}
.fcol li{list-style:none;font-size:8.2px;line-height:15.8px}
.fcol{top:48px}
.email{left:469px;top:62px;width:142px;height:23px;background:var(--white);border-radius:12px;color:#333;font-size:7.2px;padding-left:8px;display:flex;align-items:center}
.sub{left:469px;top:90px;width:142px;height:23px;border-radius:12px}
.fsoc{left:473px;top:124px;display:flex;gap:3px}
.fsoc span{width:20px;height:20px;border-radius:50%;background:var(--white)}
.fline{left:56px;top:163px;width:555px;height:1px;background:#2a2a2a}
.copy{left:0;top:175px;width:667px;text-align:center;font-size:7.4px}
</style>
</head>
<body>

<header>
  <div class="abs topbar"></div>
  <div class="abs phone">
    <span class="phone-ico"><svg width="10" height="10" viewBox="0 0 24 24"><path d="M6.6 10.8a15 15 0 0 0 6.6 6.6l2.2-2.2c.3-.3.7-.4 1-.2 1.1.4 2.3.6 3.6.6.6 0 1 .4 1 1V20c0 .6-.4 1-1 1A17 17 0 0 1 3 4c0-.6.4-1 1-1h3.5c.6 0 1 .4 1 1 0 1.3.2 2.5.6 3.6.1.3 0 .7-.2 1z" fill="none" stroke="#666" stroke-width="1.6"/></svg></span>
    555 - 014 - 2290
  </div>
  <div class="abs socials-top" aria-label="Social links"><span></span><span></span><span></span><span></span></div>
  <div class="abs brand"><span class="brand-dot"></span><span class="brand-name">THE MAPLE<br>BENCH</span></div>
  <nav>
    <span class="abs nav" style="left:56px">HOME</span>
    <span class="abs nav" style="left:108px">BENCH ACTIVITIES</span>
    <span class="abs nav" style="left:211px">BENCH EVENTS</span>
    <span class="abs nav" style="left:391px">RESOURCES</span>
    <span class="abs nav" style="left:472px">ONLINE SHOP</span>
    <span class="abs nav" style="left:560px">CONTACT US</span>
  </nav>
</header>

<section>
  <div class="abs hero" role="img" aria-label="Woman leaning over a workbench in a woodworking shop, writing on a tablet"></div>
  <h1 class="abs hero-title">BENCH EVENTS</h1>
</section>

<section>
  <h2 class="abs ws-title script"><span class="o">Workshops Organized</span> <span class="b">By The</span> <span class="p">Bench</span></h2>
  <p class="abs ws-lead">Lorem ipsum dolor sit amet, consectetur adipiscing elit, sed do eiusmod tempor incididunt ut labore et dolore magna aliqua. Quis ipsum suspendisse ultrices gravida.</p>

  <svg class="abs arrow" style="left:27px" width="10" height="18" viewBox="0 0 10 18"><path d="M9 1 1 9l8 8" fill="none" stroke="#333" stroke-width="1"/></svg>
  <svg class="abs arrow" style="left:625px" width="10" height="18" viewBox="0 0 10 18"><path d="M1 1l8 8-8 8" fill="none" stroke="#333" stroke-width="1"/></svg>

  <article class="abs card" style="left:56px">
    <div class="abs card-img" role="img" aria-label="Group of workshop participants holding certificates behind a table of power tools" style="background:linear-gradient(160deg,#6c8a5a,#4b5a48 55%,#8a8a86)"></div>
    <div class="abs date">▦ 24, OCT, 2021 &nbsp;|&nbsp; ◷ 10 AM</div>
    <h3 class="abs">Finibus Bonorum et Malorum</h3>
    <p class="abs desc">Lorem ipsum dol, consectetdipiscintd do eiusmod temporcididunt ut labore et do ipsum suspendisse ultrices gravida.</p>
    <p class="abs obj">Workshop Objectives:</p>
    <p class="abs obj-t">Finibus Bonorum et Malorum Sed ut perspiciati</p>
    <div class="abs avatar" role="img" aria-label="Host portrait" style="background:#6b4a3a"></div>
    <p class="abs host">Nora Kell</p>
    <p class="abs host-role">Finibus Bonorum et Malorum</p>
    <a class="abs btn">BOOK NOW</a>
  </article>

  <article class="abs card" style="left:244px">
    <div class="abs card-img" role="img" aria-label="Children painting at tables in a covered workshop space" style="background:linear-gradient(160deg,#c9c07a,#8a7f5a 50%,#3d3a3a)"></div>
    <div class="abs date">▦ 24, OCT, 2021 &nbsp;|&nbsp; ◷ 10 AM</div>
    <h3 class="abs">Finibus Bonorum et Malorum</h3>
    <p class="abs desc">Lorem ipsum dol, consectetdipiscintd do eiusmod temporcididunt ut labore et do ipsum suspendisse ultrices gravida.</p>
    <p class="abs obj">Workshop Objectives:</p>
    <p class="abs obj-t">Finibus Bonorum et Malorum Sed ut perspiciati</p>
    <div class="abs avatar" role="img" aria-label="Host portrait" style="background:#3a2c28"></div>
    <p class="abs host">Nora Kell</p>
    <p class="abs host-role">Finibus Bonorum et Malorum</p>
    <a class="abs btn">BOOK NOW</a>
  </article>

  <article class="abs card" style="left:432px">
    <div class="abs card-img" role="img" aria-label="Event poster for a Saturday paint and sip mixer with brushes and paint pots" style="background:linear-gradient(110deg,#d9b98a,#f2d9c4 45%,#e8c6b0 70%,#d1603a)"></div>
    <div class="abs date">▦ 24, OCT, 2021 &nbsp;|&nbsp; ◷ 10 AM</div>
    <h3 class="abs">Finibus Bonorum et Malorum</h3>
    <p class="abs desc">Lorem ipsum dol, consectetdipiscintd do eiusmod temporcididunt ut labore et do ipsum suspendisse ultrices gravida.</p>
    <p class="abs obj">Workshop Objectives:</p>
    <p class="abs obj-t">Finibus Bonorum et Malorum Sed ut perspiciati</p>
    <div class="abs avatar" role="img" aria-label="Host portrait" style="background:#a77a62"></div>
    <p class="abs host">Nora Kell</p>
    <p class="abs host-role">Finibus Bonorum et Malorum</p>
    <a class="abs btn">BOOK NOW</a>
  </article>
</section>

<section>
  <div class="abs pe-wash"></div>
  <div class="abs pe-img" role="img" aria-label="Two makers holding drills beside a wooden pallet planter they built"></div>
  <h2 class="abs pe-title script"><span class="o">Private events</span> <span class="b">Organized</span><br><span class="p">By Clients</span></h2>
  <p class="abs pe-text">Sed ut perspiciatis unde omnis iste nat errotatem accusantium<br>doloremque laudantium, totam rem aperiamaque ipsa quae ab<br>illo inventore vitatis et quasi architecto atae vit dicta sunt expo.<br>Nemo enim ipsam voluptatem quia voluptas sit aspernatur aut<br>odit aut fugit, sed quia consequuntur ni dolores eos qui ratione<br>voluptatem sequi nesciunt. Neqorro quisquam est, qui dolorem<br>ipsum quia dolor sit amet, consectetur, adi</p>
  <a class="abs btn pe-btn">CONTACT US</a>
</section>

<footer class="abs footer">
  <div class="abs fcol" style="left:56px"><h4>ABOUT</h4><ul><li>Our Story</li><li>Press</li><li>Locations</li><li>Blog</li><li>Contact Us</li></ul></div>
  <div class="abs fcol" style="left:131px"><h4>OUR OFFERING</h4><ul><li>Projects</li><li>Paint Room</li><li>Parties</li><li>Classes</li></ul></div>
  <div class="abs fcol" style="left:234px"><h4>OTHER</h4><ul><li>Franchise</li><li>Gift Cards</li><li>FAQ</li><li>Refund Policy</li></ul></div>
  <div class="abs fcol" style="left:318px"><h4>CONTACT US</h4><ul><li>48 Alder Lane Riverton USA</li><li>30417</li><li>555 - 014 - 2290</li><li>hello@maplebench.com</li></ul></div>
  <div class="abs fcol" style="left:468px"><h4>GET UPDATES &amp; PROMOS</h4></div>
  <div class="abs email">Email Address</div>
  <a class="abs btn sub">SUBSCRIBE</a>
  <div class="abs fsoc" aria-label="Social links"><span></span><span></span><span></span><span></span></div>
  <div class="abs fline"></div>
  <p class="abs copy">Copyright © 2021 The Maple Bench. All rights reserved.</p>
</footer>

</body>
</html>
```